Colin Vardek Business card

Hey there, I’m hoping to have a business card designed. I’m in Real estate and just switched to a new Brokerage called: The Harbourline Property Group

The back could just be the company name maybe or whatever looks good!

I’ve attached some logos of our company and some cards my buddy had done up.

On the card:
Colin Vardek
colinvardek@mailora.com
587-412-9065
colinvardek.ca

Target Market(s)

Home buyers and sellers

Industry/Entity Type

Real Estate

Contact Information for Business Card

just looking for a cool and modern design with my picture on it. I like the idea of Black and red being used.

Requirements
Must have
• all the details provided. I'm open to anything. Just want a professional looking card.

```html
<!DOCTYPE html>
<html lang="en">
<head>
<meta charset="utf-8">
<title>Colin Vardek – Business Card</title>
<link rel="stylesheet" href="https://fonts.googleapis.com/css2?family=Poppins:wght@300;400;600;700;800&display=swap">
<style>
  :root {
    --stage: #232323;
    --card-dark: #1f1f22;
    --brand-red: #cf213c;
    --paper-white: #ffffff;
    --text-light: #f4f4f4;
    --foil: #f0b89c;
    --photo-light: #f3f1ef;
    --photo-dark: #2a2d33;
  }
  * { box-sizing: border-box; margin: 0; padding: 0; }
  html, body {
    width: 1200px; height: 780px; overflow: hidden;
    background: var(--stage);
    font-family: "Poppins", sans-serif;
  }
  .canvas { position: relative; width: 1200px; height: 780px; }

  .card {
    position: absolute; top: 240px;
    width: 525px; height: 300px;
    overflow: hidden;
    box-shadow: 0 18px 40px rgba(0,0,0,.45);
  }
  .card--front { left: 50px; background: var(--card-dark); }
  .card--back  { left: 625px; background: var(--brand-red); }

  .front-art { position: absolute; inset: 0; }

  .front-brand {
    position: absolute; right: 28px; top: 58px;
    width: 250px; text-align: right;
    color: var(--text-light);
    font-weight: 800; font-size: 23px; line-height: 1.12;
    letter-spacing: -0.3px; text-transform: uppercase;
  }

  .agent-name {
    position: absolute; right: 28px; top: 150px;
    font-size: 30px; line-height: 1; white-space: nowrap;
  }
  .agent-name__first { color: var(--brand-red); font-weight: 700; }
  .agent-name__last  { color: var(--text-light); font-weight: 300; }

  .name-accent {
    position: absolute; right: 0; top: 146px;
    width: 10px; height: 38px; background: var(--brand-red);
  }

  .contact-list {
    position: absolute; right: 28px; top: 206px;
    list-style: none; text-align: right;
  }
  .contact-list__item {
    display: flex; justify-content: flex-end; align-items: center; gap: 8px;
    color: var(--text-light); font-size: 12.5px; font-weight: 400;
    line-height: 22px;
  }
  .contact-icon { width: 14px; height: 14px; flex: none; }

  .back-brand {
    position: absolute; inset: 0;
    display: flex; align-items: center; justify-content: center;
    text-align: center;
    color: var(--foil);
    font-weight: 800; font-size: 34px; line-height: 1.1;
    text-transform: uppercase; letter-spacing: -0.5px;
  }
</style>
</head>
<body>
<main class="canvas">

  <section class="card card--front">
    <svg class="front-art" width="525" height="300" viewBox="0 0 525 300">
      <defs>
        <linearGradient id="portraitTone" x1="0" y1="0" x2="0" y2="1">
          <stop offset="0" stop-color="var(--photo-light)"/>
          <stop offset="0.55" stop-color="#e4dcd6"/>
          <stop offset="1" stop-color="var(--photo-dark)"/>
        </linearGradient>
      </defs>
      <path d="M0 0 H190 Q268 150 150 300 H0 Z" fill="var(--paper-white)"/>
      <path d="M0 0 H176 Q248 150 138 300 H0 Z" fill="url(#portraitTone)"
            role="img" aria-label="Portrait photo of the agent in a dark blazer and white shirt"/>
      <path d="M198 0 Q278 150 160 300" fill="none" stroke="var(--brand-red)" stroke-width="7"/>
    </svg>

    <div class="front-brand">The Harbourline<br>Property Group</div>

    <h1 class="agent-name">
      <span class="agent-name__first">Colin</span>
      <span class="agent-name__last">Vardek</span>
    </h1>
    <span class="name-accent"></span>

    <ul class="contact-list">
      <li class="contact-list__item">587-412-9065
        <svg class="contact-icon" viewBox="0 0 16 16"><circle cx="8" cy="8" r="8" fill="var(--brand-red)"/><path d="M5 4.5 L6.6 4.2 L7.3 6 L6.4 6.8 Q7.2 8.6 9.2 9.6 L10 8.7 L11.8 9.4 L11.5 11 Q7 11 5 6.5 Z" fill="#fff"/></svg>
      </li>
      <li class="contact-list__item">www.colinvardek.ca
        <svg class="contact-icon" viewBox="0 0 16 16"><circle cx="8" cy="8" r="8" fill="var(--brand-red)"/><circle cx="8" cy="8" r="4.5" fill="none" stroke="#fff" stroke-width="1"/><ellipse cx="8" cy="8" rx="2" ry="4.5" fill="none" stroke="#fff" stroke-width="1"/><path d="M3.5 8 H12.5" stroke="#fff" stroke-width="1"/></svg>
      </li>
      <li class="contact-list__item">colinvardek@mailora.com
        <svg class="contact-icon" viewBox="0 0 16 16"><circle cx="8" cy="8" r="8" fill="var(--brand-red)"/><rect x="4" y="5" width="8" height="6" fill="none" stroke="#fff" stroke-width="1"/><path d="M4 5 L8 8.5 L12 5" fill="none" stroke="#fff" stroke-width="1"/></svg>
      </li>
    </ul>
  </section>

  <section class="card card--back">
    <div class="back-brand">The Harbourline<br>Property Group</div>
  </section>

</main>
</body>
</html>
```